Roofing Contractor business card redesign

I want to redesign my business card with a fresh, eye catching concept

Target Market(s)

Residential Roofing Clients, potential employees, and subcontractors.

Industry/Entity Type

Business

Colors

Designer to choose colors to be used in the design.

Requirements
Nice to have
• I just want something that's more pleasing to the eye. You can use a combination of either / or of my logos.

```html
<!DOCTYPE html>
<html lang="en">
<head>
<meta charset="utf-8">
<title>True North General Contractors – Business Card</title>
<link rel="stylesheet" href="https://fonts.googleapis.com/css2?family=Oswald:wght@500;700&family=Barlow:wght@400;500&display=swap">
<style>
  :root {
    --backdrop: #3b3b3d;
    --orange: #e66d22;
    --orange-light: #f4ad3a;
    --brown: #4a1a0e;
    --accent-yellow: #e0a613;
    --ink: #2e1a14;
    --text-grey: #4a4a4a;
    --card-white: #f4f4f4;
    --card-grey: #dcdcdc;
  }
  * { margin: 0; padding: 0; box-sizing: border-box; }
  html, body { width: 1200px; height: 960px; overflow: hidden; }
  body { background: var(--backdrop); position: relative; font-family: "Barlow", sans-serif; }

  .card {
    position: absolute;
    width: 600px;
    height: 343px;
    overflow: hidden;
    box-shadow: 2px 3px 6px rgba(0,0,0,0.45);
  }

  /* Front */
  .card-front {
    left: 320px; top: 103px;
    background: linear-gradient(135deg, var(--card-grey) 0%, var(--card-white) 35%, #e8e8e8 100%);
  }
  .front-orange {
    position: absolute; left: 425px; top: 0; width: 175px; height: 343px;
    background: var(--orange);
  }
  .illustration {
    position: absolute; left: 253px; top: 0; width: 345px; height: 343px;
  }
  .accent-bar {
    position: absolute; left: 0; top: 60px; width: 8px; height: 64px;
    background: var(--accent-yellow);
  }
  .identity { position: absolute; left: 35px; top: 56px; }
  .person-name {
    font-family: "Oswald", sans-serif; font-weight: 500;
    font-size: 27px; line-height: 34px; color: var(--orange);
    text-transform: uppercase; letter-spacing: 0.2px;
  }
  .person-title {
    font-size: 14.5px; line-height: 18px; color: var(--ink); font-weight: 500;
  }
  .address {
    position: absolute; left: 36px; top: 138px;
    font-size: 14.5px; line-height: 18px; color: var(--text-grey); font-style: normal;
  }
  .contacts { position: absolute; left: 36px; top: 208px; list-style: none; }
  .contacts li {
    display: flex; align-items: center; gap: 8px;
    font-size: 14.5px; line-height: 19px; color: var(--text-grey);
  }
  .contacts svg { width: 13px; height: 13px; flex: none; }

  /* Back */
  .card-back {
    left: 318px; top: 488px;
    background: linear-gradient(135deg, var(--orange-light) 0%, var(--orange) 40%, var(--orange) 100%);
  }
  .brand {
    position: absolute; left: 0; top: 96px; width: 600px;
    display: flex; align-items: center; justify-content: center; gap: 14px;
  }
  .brand-circle {
    width: 88px; height: 88px; border-radius: 50%;
    background: var(--brown); flex: none;
  }
  .brand-name {
    font-family: "Oswald", sans-serif; font-weight: 700; color: var(--brown);
    text-align: left;
  }
  .brand-name .line-main { display: block; font-size: 60px; line-height: 64px; letter-spacing: -1px; }
  .brand-name .line-sub { display: block; font-size: 24px; line-height: 28px; }
  .social {
    position: absolute; left: 145px; top: 284px; width: 310px; height: 26px;
    display: flex; align-items: center; justify-content: center; gap: 5px;
  }
  .social .rule { width: 75px; height: 1px; background: var(--brown); opacity: 0.7; }
  .social .rule.left { background: linear-gradient(90deg, transparent, var(--brown)); }
  .social .rule.right { background: linear-gradient(90deg, var(--brown), transparent); }
  .social .dot {
    width: 27px; height: 27px; border-radius: 50%;
    border: 1.5px solid var(--brown);
  }
</style>
</head>
<body>
  <section class="card card-front">
    <div class="front-orange"></div>
    <svg class="illustration" viewBox="0 0 345 343" role="img" aria-label="Illustrated circular badge of three roofing contractors with tools in front of a house roof">
      <defs>
        <radialGradient id="badgeFill" cx="50%" cy="45%" r="60%">
          <stop offset="0%" stop-color="#f0c23a"/>
          <stop offset="55%" stop-color="#d9692a"/>
          <stop offset="100%" stop-color="#4a2118"/>
        </radialGradient>
      </defs>
      <circle cx="173" cy="172" r="172" fill="#ffffff"/>
      <circle cx="173" cy="172" r="166" fill="url(#badgeFill)"/>
    </svg>
    <div class="accent-bar"></div>
    <div class="identity">
      <h1 class="person-name">Sam Whitley</h1>
      <p class="person-title">Ridgeline Certified Roof Inspector</p>
      <p class="person-title">Licensed Property Adjuster</p>
    </div>
    <address class="address">
      24150 Maple Ridge Road<br>
      Suite 110<br>
      Fairview, TX 75069
    </address>
    <ul class="contacts">
      <li>
        <svg viewBox="0 0 16 16"><path fill="#e66d22" d="M3.5 1.5l2.5 0 1.2 3-1.6 1.4c.8 1.8 2.2 3.2 4 4l1.4-1.6 3 1.2v2.5c0 .8-.7 1.5-1.5 1.5C6.9 13.5 2 8.6 2 3c0-.8.7-1.5 1.5-1.5z"/></svg>
        (555) 014-2200
      </li>
      <li>
        <svg viewBox="0 0 16 16"><rect x="4" y="1" width="8" height="14" rx="1.5" fill="none" stroke="#e66d22" stroke-width="1.8"/><circle cx="8" cy="12.3" r="1" fill="#e66d22"/></svg>
        (555) 016-8831
      </li>
      <li>
        <svg viewBox="0 0 16 16"><rect x="1" y="3" width="14" height="10" fill="#e66d22"/><path d="M1.5 3.5L8 9l6.5-5.5" fill="none" stroke="#f4f4f4" stroke-width="1.4"/></svg>
        sam@truenorthtx.com
      </li>
      <li>
        <svg viewBox="0 0 16 16"><circle cx="8" cy="8" r="7" fill="#e66d22"/><path d="M1.5 8h13M8 1c-2.5 2.5-2.5 11.5 0 14M8 1c2.5 2.5 2.5 11.5 0 14" fill="none" stroke="#f4f4f4" stroke-width="1"/></svg>
        truenorthtx.com
      </li>
    </ul>
  </section>

  <section class="card card-back">
    <div class="brand">
      <div class="brand-circle"></div>
      <p class="brand-name">
        <span class="line-main">True North</span>
        <span class="line-sub">General Contractors, Inc.</span>
      </p>
    </div>
    <div class="social" aria-label="Social media links">
      <span class="rule left"></span>
      <span class="dot"></span>
      <span class="dot"></span>
      <span class="dot"></span>
      <span class="dot"></span>
      <span class="dot"></span>
      <span class="rule right"></span>
    </div>
  </section>
</body>
</html>
```